Diagram of Hollowmere’s history for website

This project is to design the attached diagram along the lines of the attached image but in our branding - style guide attached. The diagram will be going on the Hollowmere website - www.hollowmere.au.

```html
<!DOCTYPE html>
<html lang="en">
<head>
<meta charset="utf-8">
<title>Hollowmere – Our History</title>
<link rel="stylesheet" href="https://fonts.googleapis.com/css2?family=Montserrat:wght@800&family=Poppins:wght@400;500;600&display=swap">
<style>
:root{
  --green:#6e8f74;
  --peach:#d6ac98;
  --slate:#8ea6ad;
  --ink:#3a3a3a;
  --paper:#ffffff;
  --backdrop:#ececea;
}
*{margin:0;padding:0;box-sizing:border-box}
html,body{width:1200px;height:1007px;overflow:hidden;background:var(--backdrop)}
.history-card{position:absolute;left:5px;top:83px;width:1190px;height:840px;background:var(--paper);overflow:hidden;font-family:"Poppins",sans-serif;color:var(--ink)}
.brand{position:absolute;left:62px;top:58px;display:flex;align-items:center;gap:14px}
.brand-dot{width:58px;height:58px;border-radius:50%;background:var(--green)}
.brand-name{font-family:"Poppins",sans-serif;font-weight:500;font-size:54px;line-height:1;color:var(--ink);letter-spacing:-0.5px}
.brand-tagline{position:absolute;left:144px;top:122px;font-size:15.5px;letter-spacing:1.6px;color:var(--ink)}
.page-title{position:absolute;left:50px;top:168px;font-family:"Montserrat",sans-serif;font-weight:800;font-size:82px;letter-spacing:7px;color:var(--ink);line-height:1}
.timeline{position:absolute;left:0;top:0}
.milestone{position:absolute;width:240px}
.milestone h3{font-weight:600;font-size:16.5px;line-height:18px;color:var(--green)}
.milestone p{font-size:12.6px;line-height:14.8px;margin-top:3px}
.footer-band{position:absolute;left:0;bottom:0;width:100%;height:27px;background:var(--green)}
</style>
</head>
<body>
<main class="history-card">
  <div class="brand"><span class="brand-dot"></span><span class="brand-name">Hollowmere</span></div>
  <div class="brand-tagline">SUPPORT • THERAPY • LEARNING</div>
  <h1 class="page-title">OUR HISTORY</h1>

  <svg class="timeline" width="1190" height="840" viewBox="0 0 1190 840" aria-label="Timeline 2017 to 2023">
    <g stroke-width="3">
      <line x1="83" y1="520" x2="83" y2="700" stroke="var(--green)"/>
      <line x1="265" y1="347" x2="265" y2="455" stroke="var(--green)"/>
      <line x1="446" y1="520" x2="446" y2="605" stroke="var(--peach)"/>
      <line x1="627" y1="305" x2="627" y2="455" stroke="var(--green)"/>
      <line x1="807" y1="520" x2="807" y2="765" stroke="var(--green)"/>
      <line x1="988" y1="62" x2="988" y2="450" stroke="var(--peach)"/>
    </g>
    <g fill="var(--green)">
      <circle cx="83" cy="549" r="5.5"/><circle cx="83" cy="661" r="5.5"/>
      <circle cx="265" cy="346" r="5.5"/>
      <circle cx="446" cy="549" r="5.5" fill="var(--green)"/>
      <circle cx="627" cy="305" r="5.5"/>
      <circle cx="807" cy="549" r="5.5"/><circle cx="807" cy="627" r="5.5"/><circle cx="807" cy="694" r="5.5"/>
      <circle cx="988" cy="62" r="5.5"/><circle cx="988" cy="110" r="5.5"/><circle cx="988" cy="159" r="5.5"/><circle cx="988" cy="206" r="5.5"/><circle cx="988" cy="300" r="5.5"/><circle cx="988" cy="379" r="5.5"/>
    </g>

    <!-- year bands -->
    <g class="year" transform="translate(83 0)">
      <polygon points="15,465 117,465 130,484 117,503 15,503" fill="var(--peach)"/>
      <polygon points="123,465 135,465 148,484 135,503 123,503 136,484" fill="var(--green)"/>
    </g>
    <g class="year" transform="translate(265 0)">
      <polygon points="15,465 117,465 130,484 117,503 15,503" fill="var(--slate)"/>
      <polygon points="123,465 135,465 148,484 135,503 123,503 136,484" fill="var(--green)"/>
    </g>
    <g class="year" transform="translate(446 0)">
      <polygon points="15,465 117,465 130,484 117,503 15,503" fill="var(--green)"/>
      <polygon points="123,465 135,465 148,484 135,503 123,503 136,484" fill="var(--peach)"/>
    </g>
    <g class="year" transform="translate(627 0)">
      <polygon points="15,465 117,465 130,484 117,503 15,503" fill="var(--slate)"/>
      <polygon points="123,465 135,465 148,484 135,503 123,503 136,484" fill="var(--green)"/>
    </g>
    <g class="year" transform="translate(807 0)">
      <polygon points="15,465 117,465 130,484 117,503 15,503" fill="var(--peach)"/>
      <polygon points="123,465 135,465 148,484 135,503 123,503 136,484" fill="var(--green)"/>
    </g>
    <g class="year" transform="translate(988 0)">
      <polygon points="15,465 117,465 130,484 117,503 15,503" fill="var(--green)"/>
      <polygon points="123,465 135,465 148,484 135,503 123,503 136,484" fill="var(--peach)"/>
    </g>

    <g font-family="Poppins, sans-serif" font-weight="600" font-size="29" fill="#fff" text-anchor="middle">
      <text x="159" y="495">2017</text>
      <text x="341" y="495">2018</text>
      <text x="522" y="495">2019</text>
      <text x="703" y="495">2021</text>
      <text x="883" y="495">2022</text>
      <text x="1064" y="495">2023</text>
    </g>

    <!-- year badges -->
    <g fill="#fff" stroke-width="5">
      <circle cx="83" cy="484" r="28" stroke="var(--green)"/>
      <circle cx="265" cy="484" r="28" stroke="var(--green)"/>
      <circle cx="446" cy="484" r="28" stroke="var(--peach)"/>
      <circle cx="627" cy="484" r="28" stroke="var(--green)"/>
      <circle cx="807" cy="484" r="28" stroke="var(--green)"/>
      <circle cx="988" cy="484" r="28" stroke="var(--peach)"/>
    </g>
    <g fill="none" stroke="#e4e4e2" stroke-width="1.5">
      <circle cx="83" cy="484" r="23"/><circle cx="265" cy="484" r="23"/><circle cx="446" cy="484" r="23"/>
      <circle cx="627" cy="484" r="23"/><circle cx="807" cy="484" r="23"/><circle cx="988" cy="484" r="23"/>
    </g>

    <!-- icons -->
    <g fill="var(--ink)" stroke="var(--ink)">
      <g class="icon-board" stroke-width="2" fill="none">
        <rect x="71" y="472" width="17" height="12"/><line x1="79" y1="484" x2="79" y2="496"/><line x1="74" y1="496" x2="84" y2="496"/><line x1="91" y1="476" x2="96" y2="472"/>
      </g>
      <g class="icon-building">
        <polygon points="253,478 265,470 277,478" stroke="none"/>
        <rect x="254" y="480" width="22" height="14" fill="none" stroke-width="2"/>
        <rect x="258" y="484" width="3" height="8" stroke="none"/><rect x="264" y="484" width="3" height="8" stroke="none"/><rect x="270" y="484" width="3" height="8" stroke="none"/>
      </g>
      <g class="icon-route" fill="none" stroke-width="2">
        <circle cx="452" cy="475" r="4"/><path d="M452 483 C452 486 440 484 440 490 C440 495 452 492 452 497"/><circle cx="440" cy="491" r="2" fill="var(--ink)"/>
      </g>
      <g class="icon-org" stroke="none">
        <rect x="621" y="470" width="12" height="9"/><rect x="615" y="487" width="8" height="8"/><rect x="631" y="487" width="8" height="8"/>
        <rect x="626" y="479" width="2" height="5"/><rect x="619" y="483" width="16" height="2"/>
      </g>
      <g class="icon-meeting" fill="none" stroke-width="2">
        <line x1="796" y1="489" x2="818" y2="489"/><line x1="800" y1="489" x2="800" y2="497"/><line x1="814" y1="489" x2="814" y2="497"/><circle cx="807" cy="477" r="3.5"/>
      </g>
      <g class="icon-gear" fill="none" stroke-width="2">
        <circle cx="988" cy="484" r="12" stroke-dasharray="4 2.3"/><circle cx="988" cy="484" r="7"/>
        <polygon points="988,479 989.5,483 993,483 990,485.5 991,489 988,487 985,489 986,485.5 983,483 986.5,483" fill="var(--ink)" stroke="none"/>
      </g>
    </g>
  </svg>

  <div class="milestone" style="left:101px;top:538px">
    <h3>Hollowmere Commences</h3>
    <p>Maren started the business with<br>25 years’ experience working for<br>government &amp; non- government<br>disability &amp; community services.<br>Our first office is in Ashbury</p>
  </div>
  <div class="milestone" style="left:101px;top:651px">
    <h3>NCSS Provider</h3>
    <p>Hollowmere becomes a NCSS<br>Registered provider</p>
  </div>
  <div class="milestone" style="left:283px;top:336px">
    <h3>Clinic Expansion</h3>
    <p>Hollowmere moves<br>offices twice in Ashbury<br>due to growth &amp;<br>expansion. Clinic<br>established</p>
  </div>
  <div class="milestone" style="left:464px;top:538px">
    <h3>Move to Fernleigh</h3>
    <p>Hollowmere moves to Fernleigh<br>due to further growth &amp;<br>expansion</p>
  </div>
  <div class="milestone" style="left:645px;top:295px">
    <h3>Impact-Certified</h3>
    <p>Hollowmere becomes an<br>accredited<br>Impact-Certified business<br>having met the highest<br>standards of<br>environmental, social &amp;<br>community<br>performance</p>
  </div>
  <div class="milestone" style="left:825px;top:538px">
    <h3>Telvarra Best of</h3>
    <p>Hollowmere wins the Telvarra Best<br>of Business Award (Vic) for<br>building communities</p>
  </div>
  <div class="milestone" style="left:825px;top:617px">
    <h3>Move to Kellbrook</h3>
    <p>Hollowmere moves to a larger<br>premises in Kellbrook</p>
  </div>
  <div class="milestone" style="left:825px;top:683px">
    <h3>Partnerships</h3>
    <p>Partnerships established with<br>Coral Bay School for Children with<br>Disability &amp; Wattle Circle<br>(Southbank University)</p>
  </div>
  <div class="milestone" style="left:1002px;top:52px;width:180px">
    <h3>Rebranding</h3>
    <p>Hollowmere rebranded</p>
  </div>
  <div class="milestone" style="left:1002px;top:99px;width:180px">
    <h3>Reconciliation<br>Action Plan (RAP)</h3>
    <p>Hollowmere’s Reflect<br>RAP developed &amp;<br>endorsed</p>
  </div>
  <div class="milestone" style="left:1002px;top:196px;width:180px">
    <h3>Client Advisory<br>Group</h3>
    <p>Hollowmere’s Client<br>Advisory Group<br>commences</p>
  </div>
  <div class="milestone" style="left:1002px;top:290px;width:180px">
    <h3>E-Learning<br>Platform</h3>
    <p>Hollowmere e-learning<br>platform launched</p>
  </div>
  <div class="milestone" style="left:1002px;top:369px;width:180px">
    <h3>Pride Mark</h3>
    <p>Hollowmere achieves<br>Pride Mark<br>accreditation</p>
  </div>

  <div class="footer-band"></div>
</main>
</body>
</html>
```